Website design with eCommerce for revolutionary new product in the manufacturing industry.

We need a website designed for a precision manufacturing company based in the suburbs of Minneapolis, Minnesota called Velkrin Manufacturing. We have a revolutionary new product, the TARN LOCK, to introduce and sell through an eCommerce storefront. The website would include company information, product information, and the storefront. Green is a color that represents Velkrin Manufacturing. The final design should communicate that we exclusively offer premium products at a premium price. The design should also let the customer know they are the focus of our work.

Target Market(s)

Machinists and machine shops

Industry/Entity Type

Manufacturing and machine shops

Coding

Coded - Design and coding required

Font styles to use
Sans Serif

Colors
59FF00
82FF00
B8FF75
E3FFCB
F4FFEA

Requirements
Must have
• eCommerce storefront, Made in USA references
Nice to have
• Home page, TARN LOCK Product page, About Us, Capabilities, Contact, etc.
Should not have
• Should not be too much text and reading.

```html
<!DOCTYPE html>
<html lang="en">
<head>
<meta charset="utf-8">
<title>Velkrin Manufacturing – Home of the TARN LOCK</title>
<link rel="stylesheet" href="https://fonts.googleapis.com/css2?family=Outfit:wght@300;400;500;600;700;800&display=swap">
<style>
:root{
  --green:#1f8f2c;
  --green-bright:#5fd13a;
  --green-label:#3a9a2e;
  --ink:#111;
  --text:#555;
  --line:#e3e3e3;
  --white:#fff;
}
*{margin:0;padding:0;box-sizing:border-box}
html,body{width:1200px;height:3659px;overflow:hidden}
body{font-family:"Outfit",sans-serif;color:var(--ink);background:var(--white);position:relative}
.abs{position:absolute}
a{color:inherit;text-decoration:none}

/* header */
.site-header{position:absolute;left:0;top:0;width:1200px;height:71px;background:var(--white)}
.brand{position:absolute;display:flex;align-items:center;gap:8px;font-weight:800;font-size:24px;letter-spacing:1px;color:var(--ink)}
.brand .mark{width:16px;height:16px;background:var(--ink)}
.site-header .brand{left:159px;top:22px}
.main-nav{position:absolute;left:390px;top:28px;display:flex;gap:28px;font-size:12px;font-weight:500;letter-spacing:.4px}
.main-nav .active{display:flex;align-items:center;gap:5px}
.phone{position:absolute;left:918px;top:24px;display:flex;align-items:center;gap:8px;font-weight:700;font-size:15px}

/* hero */
.hero{position:absolute;left:0;top:71px;width:1200px;height:491px;background:radial-gradient(circle at 30% 40%,#2d2b28,#151412 70%)}
.hero-title{position:absolute;left:156px;top:180px;font-size:46px;font-weight:800;line-height:48px;color:var(--white);letter-spacing:.5px}
.hero-title .accent{color:var(--green-bright)}
.hero-sub{position:absolute;left:158px;top:285px;width:360px;font-size:14px;font-weight:500;color:var(--white);line-height:19px}
.btn-outline{position:absolute;display:flex;align-items:center;justify-content:center;border:1px solid var(--white);color:var(--white);font-size:13px;font-weight:500;letter-spacing:.4px;border-radius:2px}
.hero .btn-outline{left:158px;top:349px;width:130px;height:37px}
.hero-frame{position:absolute;left:708px;top:64px;width:380px;height:412px;border:1.5px solid var(--green-bright);transform:skewX(-4deg);border-radius:6px}
.hero-photo{position:absolute;left:692px;top:50px;width:373px;height:412px;background:linear-gradient(160deg,#9fb0bf,#3f5668 55%,#23303a);clip-path:polygon(7% 0,100% 0,93% 100%,0 100%);border-radius:6px}

/* why */
.scroll-arrow{position:absolute;left:590px;top:597px}
.label{position:absolute;width:1200px;text-align:center;font-size:12px;font-weight:500;color:var(--green-label)}
.headline{position:absolute;width:1200px;text-align:center;font-size:22px;font-weight:500;line-height:24px;text-transform:uppercase}
.feature{position:absolute;top:809px;display:flex;align-items:center;gap:16px}
.feature .icon-box{width:62px;height:57px;border:1px solid #d8d8d8;border-radius:4px;display:flex;align-items:center;justify-content:center}
.feature p{font-size:13.5px;color:var(--text);line-height:16px;width:175px}
.feature.narrow p{width:110px}

/* what we do */
.what{position:absolute;left:0;top:939px;width:1200px;height:414px;background:radial-gradient(circle at 20% 50%,#3a3632,#1d1b19 75%)}
.section-title{display:flex;align-items:center;gap:8px;font-size:22px;font-weight:600;text-transform:uppercase}
.what .section-title{position:absolute;left:158px;top:62px;color:var(--white)}
.what .section-title .accent{color:var(--green-bright)}
.what-lead{position:absolute;left:156px;top:94px;width:330px;font-size:17px;font-weight:600;line-height:20px;color:var(--white)}
.what-body{position:absolute;left:156px;top:140px;width:330px;font-size:11.5px;color:#ddd;line-height:15.5px}
.what-body p+p{margin-top:14px}
.what .btn-outline{left:158px;top:315px;width:130px;height:37px}
.what-photo{position:absolute;left:525px;top:34px;width:675px;height:380px;background:linear-gradient(120deg,#a59a88,#6e6252 45%,#3d4a63);clip-path:polygon(6% 0,100% 0,100% 100%,0 100%);border-radius:6px 0 0 0}

/* gallery */
.gallery-item{position:absolute;top:1518px;width:232px;height:240px}
.slider-btn{position:absolute;top:1800px;width:29px;height:28px;display:flex;align-items:center;justify-content:center}

/* how */
.how{position:absolute;left:0;top:1898px;width:1200px;height:391px;background:linear-gradient(120deg,#f4f4f4,#e9e9e9)}
.how-photo{position:absolute;left:163px;top:56px;width:388px;height:280px;background:linear-gradient(135deg,#2c4a9a,#1a2a55 50%,#6b5a3a);clip-path:polygon(7% 0,100% 0,93% 100%,0 100%);border-radius:8px}
.how .section-title{position:absolute;left:596px;top:56px;color:var(--ink)}
.how-list{position:absolute;left:596px;top:108px;width:400px;list-style:none}
.how-list li{display:flex;gap:12px;font-size:11.5px;color:var(--text);line-height:17px;margin-bottom:17px}
.how-list svg{flex:none;margin-top:2px}
.btn-solid{position:absolute;display:flex;align-items:center;justify-content:center;color:var(--white);font-size:13px;font-weight:500;letter-spacing:.4px;border-radius:3px}
.how .btn-solid{left:598px;top:286px;width:130px;height:37px;background:#111}

/* capabilities */
.cap{position:absolute;width:240px}
.cap h3{font-size:16px;font-weight:500;margin-top:14px;display:flex;align-items:center;gap:8px}
.cap h3::after{content:"";width:14px;height:1px;background:var(--green)}
.cap p{font-size:12px;color:var(--text);line-height:15.5px;margin-top:6px;width:205px}
.cap .go{margin-top:14px;display:block}
.divider-v{position:absolute;width:1px;background:var(--line)}
.divider-h{position:absolute;height:1px;background:var(--line)}
.btn-green{background:var(--green)}

/* contact */
.contact{position:absolute;left:0;top:3025px;width:1200px;height:457px;background:radial-gradient(circle at 50% 50%,#262626,#141414 75%)}
.contact .section-title{position:absolute;left:157px;top:70px;color:var(--white)}
.field{position:absolute;left:158px;width:325px;height:36px;border:1px solid #8a8a8a;border-radius:3px;font-size:12px;color:#9a9a9a;padding:10px 14px}
.contact .btn-solid{left:158px;top:357px;width:110px;height:34px;background:var(--green)}
.contact-photo{position:absolute;left:542px;top:82px;width:435px;height:280px;background:linear-gradient(135deg,#d9dde2,#9ea8b3 40%,#c9d24a 75%,#6b6f3a);clip-path:polygon(7% 0,100% 0,93% 100%,0 100%);border-radius:8px}

/* footer */
.site-footer .brand{left:161px;top:3537px}
.footer-nav{position:absolute;left:437px;top:3544px;display:flex;gap:24px;font-size:12px;font-weight:500;letter-spacing:.3px}
.footer-nav .sep{color:#444}
.footer-rule{position:absolute;left:0;top:3590px;width:1200px;height:1px;background:var(--line)}
.copyright{position:absolute;left:159px;top:3615px;font-size:11px;color:#333}
.social{position:absolute;left:927px;top:3609px;display:flex;gap:6px}
.social span{width:22px;height:22px;border-radius:50%;background:#cfcfcf}
.social span:first-child{background:var(--green)}
</style>
</head>
<body>

<header class="site-header">
  <div class="brand"><span class="mark"></span>VELKRIN</div>
  <nav class="main-nav">
    <a class="active" href="#"><svg width="12" height="8" viewBox="0 0 12 8"><path d="M0 4h10M7 1l3 3-3 3" stroke="#1f8f2c" stroke-width="1.6" fill="none"/></svg>HOME</a>
    <a href="#">CAPABILITIES</a><a href="#">ABOUT US</a><a href="#">GALLERY</a><a href="#">WISDOM</a><a href="#">CONTACT US</a>
  </nav>
  <div class="phone"><svg width="20" height="20" viewBox="0 0 24 24"><path d="M6.6 10.8a15 15 0 0 0 6.6 6.6l2.2-2.2a1 1 0 0 1 1-.25 11 11 0 0 0 3.6.6 1 1 0 0 1 1 1V20a1 1 0 0 1-1 1A17 17 0 0 1 3 4a1 1 0 0 1 1-1h3.5a1 1 0 0 1 1 1 11 11 0 0 0 .6 3.6 1 1 0 0 1-.25 1z" fill="#111"/></svg>555 014 2290</div>
</header>

<section class="hero">
  <h1 class="hero-title">WELCOME TO <span class="accent">VELKRIN</span><br>MANUFACTURING</h1>
  <p class="hero-sub">We are a machine shop with complete end to end manufacturing capabilities.</p>
  <a class="btn-outline" href="#tarn-lock-store">SHOP NOW</a>
  <div class="hero-frame"></div>
  <div class="hero-photo" role="img" aria-label="Machinist in a blue shirt standing at a machine in the shop"></div>
</section>

<svg class="scroll-arrow" width="20" height="30" viewBox="0 0 20 30"><path d="M10 0v28M2 20l8 8 8-8" stroke="#333" stroke-width="1.4" fill="none"/></svg>
<div class="label" style="top:669px">Why Velkrin Manufacturing?</div>
<h2 class="headline" style="top:696px">Because there is a better way, and we will find it,<br>even if it’s the hard way.&nbsp; We believe in working<br>harder and smarter to achieve success.</h2>

<div class="feature" style="left:158px">
  <div class="icon-box"><svg width="32" height="32" viewBox="0 0 32 32" fill="none" stroke="#333" stroke-width="1.3"><path d="M4 28h24M7 28V20h3v8M13 28V16h3v8M19 28V12h3v16M25 28V8h3"/><circle cx="25" cy="5" r="2" stroke="#1f8f2c"/></svg></div>
  <p>Our success is measured in your success</p>
</div>
<div class="feature" style="left:473px">
  <div class="icon-box"><svg width="32" height="32" viewBox="0 0 32 32" fill="none" stroke="#333" stroke-width="1.3"><circle cx="15" cy="17" r="11"/><circle cx="15" cy="17" r="6"/><circle cx="15" cy="17" r="1.5"/><path d="M15 17L27 5M24 5h3v3" stroke="#1f8f2c"/></svg></div>
  <p>Focused on our your needs and making excellent parts</p>
</div>
<div class="feature narrow" style="left:802px">
  <div class="icon-box"><svg width="32" height="32" viewBox="0 0 32 32" fill="none" stroke="#333" stroke-width="1.3"><path d="M4 28h24M4 28V6"/><path d="M6 24l6-7 5 4 8-10"/><circle cx="24" cy="7" r="3" stroke="#1f8f2c"/></svg></div>
  <p>Exceeding your expectations</p>
</div>

<section class="what">
  <h2 class="section-title">What we <span class="accent">do</span><svg width="48" height="18" viewBox="0 0 48 18" fill="none" stroke="#5fd13a" stroke-width="1.4"><path d="M0 6h40M0 12h40M36 1l10 8-10 8"/></svg></h2>
  <p class="what-lead">We are a machine shop with complete end to end manufacturing capabilities.</p>
  <div class="what-body">
    <p>We can take an idea or need, and bring it to a complete physical product.&nbsp; We can design and build your prototype, and we can mass produce it too.</p>
    <p>We love working directly with customers to manufacture their products, and help make it better where appropriate.&nbsp; We can work with as little as a verbal description, up to following fully defined customer specifications.</p>
  </div>
  <a class="btn-outline" href="#">LEARN MORE</a>
  <div class="what-photo" role="img" aria-label="Two machinists wearing safety goggles working at a bench"></div>
</section>

<div class="label" style="top:1413px">Gallery</div>
<h2 class="headline" style="top:1441px">Here are some of the projects we’ve<br>created over the years.</h2>

<div class="gallery-item" style="left:-128px;background:linear-gradient(135deg,#3d5b8c,#c9a66b)" role="img" aria-label="Machined aluminium brackets on a blue surface"></div>
<div class="gallery-item" style="left:117px;background:linear-gradient(135deg,#b7b2a8,#6f6a62)" role="img" aria-label="Rows of machined metal rings"></div>
<div class="gallery-item" style="left:362px;background:linear-gradient(135deg,#3a3a3a,#9a9a9a 50%,#2b2b2b)" role="img" aria-label="Machined carbon and metal hub part"></div>
<div class="gallery-item" style="left:606px;background:linear-gradient(135deg,#8d8a84,#3c3a36)" role="img" aria-label="Grid of machined metal parts"></div>
<div class="gallery-item" style="left:851px;background:radial-gradient(circle,#d4d4d4,#9a9a9a 45%,#7d7d7d)" role="img" aria-label="Perforated round metal disc"></div>
<div class="gallery-item" style="left:1096px;background:linear-gradient(135deg,#5a5a5a,#c8c8c8)" role="img" aria-label="Machined metal part close-up"></div>

<div class="slider-btn" style="left:568px;background:#d9d9d9"><svg width="8" height="12" viewBox="0 0 8 12"><path d="M7 1L2 6l5 5" stroke="#333" stroke-width="1.4" fill="none"/></svg></div>
<div class="slider-btn" style="left:603px;background:var(--green-bright)"><svg width="8" height="12" viewBox="0 0 8 12"><path d="M1 1l5 5-5 5" stroke="#111" stroke-width="1.4" fill="none"/></svg></div>

<section class="how">
  <svg class="abs" style="left:0;top:0" width="150" height="150" viewBox="0 0 150 150"><path d="M0 0H125L148 30L0 150Z" fill="#1f8f2c"/></svg>
  <svg class="abs" style="left:1075px;top:241px" width="125" height="150" viewBox="0 0 125 150"><path d="M125 0V150H40L0 90Z" fill="#1f8f2c"/></svg>
  <div class="how-photo" role="img" aria-label="Welder in protective gear welding with blue sparks"></div>
  <h2 class="section-title">How we make it better<svg width="48" height="18" viewBox="0 0 48 18" fill="none" stroke="#5fd13a" stroke-width="1.4"><path d="M0 6h40M0 12h40M36 1l10 8-10 8"/></svg></h2>
  <ul class="how-list">
    <li><svg width="15" height="15" viewBox="0 0 16 16" fill="none" stroke="#333" stroke-width="1.3"><circle cx="8" cy="8" r="6.5"/><path d="M5 8l2.2 2.2L14 3"/></svg>With 100 years of combined knowledge and experience to draw upon, we find solutions.</li>
    <li><svg width="15" height="15" viewBox="0 0 16 16" fill="none" stroke="#333" stroke-width="1.3"><circle cx="8" cy="8" r="6.5"/><path d="M5 8l2.2 2.2L14 3"/></svg>Our vast experience across multiple industries gives us insight that is invaluable in creativity and foresight.</li>
    <li><svg width="15" height="15" viewBox="0 0 16 16" fill="none" stroke="#333" stroke-width="1.3"><circle cx="8" cy="8" r="6.5"/><path d="M5 8l2.2 2.2L14 3"/></svg>This real life experience brings a broader understanding of what works, and more importantly, what doesn’t work, ultimately allowing us to make more informed decisions.</li>
  </ul>
  <a class="btn-solid" href="#">LEARN MORE</a>
</section>

<div class="label" style="top:2352px">What can we do?</div>
<h2 class="headline" style="top:2374px">While this list covers much of our capabilities, it<br>is by no means exhaustive. You can always<br>contact us with specific requests.</h2>

<div class="divider-v" style="left:427px;top:2500px;height:345px"></div>
<div class="divider-v" style="left:760px;top:2500px;height:345px"></div>
<div class="divider-h" style="left:148px;top:2677px;width:895px"></div>

<div class="cap" style="left:158px;top:2495px">
  <svg width="50" height="46" viewBox="0 0 50 46" fill="none" stroke="#222" stroke-width="1.4"><rect x="2" y="2" width="46" height="32" rx="2"/><path d="M18 44h14M25 34v10"/><path d="M14 10h22v16H14z" stroke="#1f8f2c"/><path d="M14 10l6 6h10l6-6M20 16v10M30 16v10"/></svg>
  <h3>CAD Design</h3>
  <p>Do you have something that needs to be created, but no method of capturing the design?</p>
  <svg class="go" width="20" height="12" viewBox="0 0 20 12"><path d="M0 6h18M13 1l5 5-5 5" stroke="#111" stroke-width="1.5" fill="none"/></svg>
</div>
<div class="cap" style="left:488px;top:2495px">
  <svg width="50" height="46" viewBox="0 0 50 46" fill="none" stroke="#222" stroke-width="1.4"><rect x="2" y="2" width="46" height="40" rx="3"/><path d="M2 11h46"/><circle cx="8" cy="6.5" r="1.3"/><circle cx="13" cy="6.5" r="1.3"/><circle cx="18" cy="6.5" r="1.3"/><path d="M19 20l-6 6 6 6M31 20l6 6-6 6M28 18l-6 16" stroke="#1f8f2c"/></svg>
  <h3>CAM Programming</h3>
  <p>Do you need programs for your machines? Perhaps we can help. We use the latest 3D CAM</p>
  <svg class="go" width="20" height="12" viewBox="0 0 20 12"><path d="M0 6h18M13 1l5 5-5 5" stroke="#111" stroke-width="1.5" fill="none"/></svg>
</div>
<div class="cap" style="left:819px;top:2495px">
  <svg width="50" height="46" viewBox="0 0 50 46" fill="none" stroke="#222" stroke-width="1.4"><rect x="4" y="2" width="38" height="32" rx="2"/><path d="M14 42h18M23 34v8"/><path d="M23 8l9 5v10l-9 5-9-5V13z M14 13l9 5 9-5M23 18v10" stroke="#1f8f2c"/></svg>
  <h3>FFF 3D Printing</h3>
  <p>Do you need a quick sample? Using Fused Filament Fabrication we can 3D print prototypes for</p>
  <svg class="go" width="20" height="12" viewBox="0 0 20 12"><path d="M0 6h18M13 1l5 5-5 5" stroke="#111" stroke-width="1.5" fill="none"/></svg>
</div>
<div class="cap" style="left:158px;top:2700px">
  <svg width="50" height="46" viewBox="0 0 50 46" fill="none" stroke="#222" stroke-width="1.4"><rect x="2" y="16" width="44" height="26" rx="2"/><path d="M8 24h18M8 30h24M8 36h14"/><circle cx="23" cy="8" r="5" stroke="#1f8f2c"/><path d="M21 13v3h4v-3" stroke="#1f8f2c"/><rect x="38" y="20" width="6" height="18" rx="1"/></svg>
  <h3>Prototypes</h3>
  <p>Do you need a custom part, or test sample?<br>We can make custom, one-off parts such as racing components.</p>
  <svg class="go" width="20" height="12" viewBox="0 0 20 12"><path d="M0 6h18M13 1l5 5-5 5" stroke="#111" stroke-width="1.5" fill="none"/></svg>
</div>
<div class="cap" style="left:488px;top:2700px">
  <svg width="50" height="46" viewBox="0 0 50 46" fill="none" stroke="#222" stroke-width="1.4"><path d="M4 2h42v6H4zM12 8h26l-4 10H16z"/><path d="M25 18v10" stroke="#1f8f2c"/><path d="M21 28h8l-4 6z" stroke="#1f8f2c"/><path d="M6 38h38v6H6z"/></svg>
  <h3>Vertical CNC Machining</h3>
  <p>with simultaneous 4th axis rotary<br>If you need parts processed through a vertical machining center, let us know.</p>
  <svg class="go" width="20" height="12" viewBox="0 0 20 12"><path d="M0 6h18M13 1l5 5-5 5" stroke="#111" stroke-width="1.5" fill="none"/></svg>
</div>
<div class="cap" style="left:817px;top:2700px">
  <svg width="50" height="46" viewBox="0 0 50 46" fill="none" stroke="#222" stroke-width="1.4"><path d="M12 2h26v8H12zM16 10h18l-4 10H20z"/><path d="M25 20v8M20 26l10 6M30 26l-10 6" stroke="#1f8f2c"/><path d="M10 40h30v4H10z"/></svg>
  <h3>CNC Turning</h3>
  <p>Collet or chuck work<br>If you need parts processed through a CNC lathe, let us know.</p>
  <svg class="go" width="20" height="12" viewBox="0 0 20 12"><path d="M0 6h18M13 1l5 5-5 5" stroke="#111" stroke-width="1.5" fill="none"/></svg>
</div>

<a class="btn-solid btn-green" href="#" style="left:504px;top:2915px;width:192px;height:37px">VIEW ALL CAPABILITIES</a>

<section class="contact">
  <h2 class="section-title">Get in touch with us</h2>
  <div class="field" style="top:113px">Name :</div>
  <div class="field" style="top:156px">Email :</div>
  <div class="field" style="top:200px">Phone :</div>
  <div class="field" style="top:244px;height:104px">Message :</div>
  <a class="btn-solid" href="#">SUBMIT</a>
  <div class="contact-photo" role="img" aria-label="Two workers in hard hats and safety vests in a factory"></div>
</section>

<footer class="site-footer">
  <div class="brand"><span class="mark"></span>VELKRIN</div>
  <nav class="footer-nav">
    <a href="#">HOME</a><span class="sep">I</span><a href="#">CAPABILITIES</a><span class="sep">I</span><a href="#">ABOUT US</a><span class="sep">I</span><a href="#">GALLERY</a><span class="sep">I</span><a href="#">WISDOM</a><span class="sep">I</span><a href="#">CONTACT US</a>
  </nav>
  <div class="footer-rule"></div>
  <p class="copyright">© Copyright 2022 Velkrin Manufacturing | TARN LOCK – Made in USA | All rights reserved.</p>
  <div class="social"><span></span><span></span><span></span><span></span></div>
</footer>

</body>
</html>
```